Norrell Advisory WA Business Card

Create an interesting, eye catching and colourful two sided business card. We are a business consulting operation assisting SME's improve all areas of their business. We provide consulting services to assist SME's to create a culture of continuous improvement, making a positive difference in the business. Our tag line is Small changes, big rewards. We want to create a well recognised, innovative brand that can be continued throughout our website, social media and email correspondence.

Target Market(s)

Small to Medium Enterprise Business Owners

Industry/Entity Type

Business Consultant

Contact Information for Business Card

Name of Business: Norrell Advisory - Small Changes Big Rewards
Derek Holloway Ph 0407385510 Megan Holloway Ph 0407913847
Email norrelladvisorywa@mailbox-example.com
Web address TBA
FaceBook page TBA

BACKSIDE OF CARD

Providing assistance with:

• Organisation & Efficiency
• Revenue generation & Marketing
• Financial Management
• Production quality & delivery
• Systems & Process documentation
• Exit Strategy

Font styles to use
Other font styles liked:
• Calibri

Colors

Designer to choose colors to be used in the design.

Requirements
Must have
• Calibri font

```html
<!DOCTYPE html>
<html lang="en">
<head>
<meta charset="utf-8">
<title>Norrell Advisory WA Business Card</title>
<link rel="stylesheet" href="https://fonts.googleapis.com/css2?family=Open+Sans:ital,wght@0,400;0,600;0,700;1,700&display=swap">
<style>
  :root {
    --page-bg: #e4e1dd;
    --card-light: #f7f7f6;
    --card-mid: #e9ecef;
    --card-cool: #dfe8f0;
    --ink-dark: #2b2b2b;
    --ink-grey: #4a4a4a;
    --name-blue: #163b63;
    --band-dark: #262626;
    --band-text: #c9bfb8;
    --accent-blue: #1f6fb2;
    --accent-red: #d2232a;
    --accent-green: #5a9e2f;
    --accent-orange: #e8a21c;
  }
  * { box-sizing: border-box; margin: 0; padding: 0; }
  html, body {
    width: 1200px; height: 969px; overflow: hidden;
    background: var(--page-bg);
    font-family: "Open Sans", Arial, sans-serif;
  }
  .card {
    position: absolute; left: 100px; top: 200px;
    width: 1000px; height: 570px;
    background: linear-gradient(120deg, var(--card-light) 0%, var(--card-mid) 45%, var(--card-cool) 100%);
    box-shadow: 0 10px 30px rgba(0,0,0,0.18);
    overflow: hidden;
  }
  .brand {
    position: absolute; left: 60px; top: 250px; width: 470px;
    text-align: center;
  }
  .brand-name {
    font-weight: 700; font-size: 36px; letter-spacing: 0.5px;
    color: var(--ink-dark); text-transform: uppercase; line-height: 1;
  }
  .brand-tagline {
    margin-top: 10px;
    font-weight: 400; font-size: 21px; letter-spacing: 1.5px;
    color: var(--ink-grey); text-transform: uppercase; line-height: 1;
  }
  .people { position: absolute; left: 538px; top: 80px; }
  .person-name {
    font-weight: 700; font-size: 33px; color: var(--name-blue);
    line-height: 1; letter-spacing: 0.5px; text-transform: uppercase;
  }
  .person-phone {
    font-weight: 700; font-size: 21px; color: var(--ink-dark);
    line-height: 1; margin-top: 8px;
  }
  .person + .person { margin-top: 20px; }
  .contacts { position: absolute; left: 550px; top: 252px; list-style: none; }
  .contact {
    display: flex; align-items: center; gap: 12px;
    font-size: 21px; color: var(--ink-dark); height: 30px;
  }
  .contact svg, .contact .social-square { width: 16px; height: 16px; flex: none; }
  .social-square { background: var(--ink-grey); display: block; }
  .services {
    position: absolute; left: 0; top: 398px; width: 1000px; height: 145px;
    background: var(--band-dark); text-align: center;
  }
  .rule {
    position: absolute; left: 0; width: 100%; height: 4px; display: flex; gap: 4px;
  }
  .rule span { flex: 1; }
  .rule .blue { background: var(--accent-blue); }
  .rule .red { background: var(--accent-red); }
  .rule .green { background: var(--accent-green); }
  .rule .orange { background: var(--accent-orange); }
  .rule.top { top: 2px; }
  .rule.bottom { bottom: 2px; }
  .services-heading {
    padding-top: 20px;
    font-weight: 700; font-style: italic; font-size: 29px;
    color: var(--accent-blue); line-height: 1.1;
  }
  .services-line {
    font-size: 21px; color: var(--band-text); line-height: 1.45; margin-top: 2px;
  }
  .services-line + .services-line { margin-top: 0; }
  .dot { color: var(--accent-blue); margin: 0 6px; font-size: 16px; }
</style>
</head>
<body>
  <div class="card">
    <div class="brand">
      <div class="brand-name">Norrell Advisory</div>
      <div class="brand-tagline">Small Changes Big Rewards</div>
    </div>

    <div class="people">
      <div class="person">
        <div class="person-name">Derek Holloway</div>
        <div class="person-phone">0407385510</div>
      </div>
      <div class="person">
        <div class="person-name">Megan Holloway</div>
        <div class="person-phone">0407913847</div>
      </div>
    </div>

    <ul class="contacts">
      <li class="contact">
        <svg viewBox="0 0 16 16" aria-hidden="true"><rect x="1" y="3" width="14" height="10" fill="#4a4a4a"/><path d="M1 3 L8 9 L15 3" fill="none" stroke="#e9ecef" stroke-width="1.4"/></svg>
        norrelladvisorywa@mailbox-example.com
      </li>
      <li class="contact">
        <svg viewBox="0 0 16 16" aria-hidden="true"><circle cx="8" cy="8" r="7" fill="#4a4a4a"/><path d="M1 8 H15 M8 1 C4 5 4 11 8 15 M8 1 C12 5 12 11 8 15" fill="none" stroke="#e9ecef" stroke-width="1"/></svg>
        www.norrelladvisorywa-example.com
      </li>
      <li class="contact">
        <span class="social-square" aria-hidden="true"></span>
        norrelladvisorywa
      </li>
    </ul>

    <section class="services">
      <div class="rule top"><span class="blue"></span><span class="red"></span><span class="green"></span><span class="orange"></span></div>
      <h2 class="services-heading">Providing assistance with</h2>
      <p class="services-line">Organisation &amp; Efficiency<span class="dot">•</span>Revenue generation &amp; Marketing<span class="dot">•</span>Financial Management</p>
      <p class="services-line">Production quality &amp; delivery<span class="dot">•</span>Systems &amp; Process documentation<span class="dot">•</span>Exit Strategy</p>
      <div class="rule bottom"><span class="blue"></span><span class="red"></span><span class="green"></span><span class="orange"></span></div>
    </section>
  </div>
</body>
</html>
```